Business card design for my company.
I would like the card's background colour to be black. You can also see our web site to get an idea of our brand. https://www.tmwhomecrafting.com.au/
- Name
- Email

```html
<!DOCTYPE html>
<html lang="en">
<head>
<meta charset="utf-8">
<title>TMW Home Crafting – Business Card</title>
<link rel="stylesheet" href="https://fonts.googleapis.com/css2?family=Roboto:wght@300;400;700;900&display=swap">
<style>
  :root {
    --stage: #2a2a2c;
    --card-black: #1c1c1f;
    --card-dark: #232327;
    --pattern: #262629;
    --green: #1a9a4a;
    --white: #ffffff;
    --muted: #e8e8e8;
  }
  * { margin: 0; padding: 0; box-sizing: border-box; }
  html, body {
    width: 1200px; height: 800px; overflow: hidden;
    background: var(--stage);
    font-family: "Roboto", sans-serif;
  }
  .stage { position: relative; width: 1200px; height: 800px; }

  .card {
    position: absolute;
    width: 560px; height: 320px;
    border-radius: 28px;
    overflow: hidden;
    border-left: 5px solid var(--green);
    border-bottom: 5px solid var(--green);
    box-shadow: 0 18px 40px rgba(0,0,0,0.45);
  }

  /* Front */
  .card-front { left: 120px; top: 70px; background: var(--card-black); }
  .front-texture {
    position: absolute; inset: 0;
    background: linear-gradient(160deg, #2b2b2f 0%, var(--pattern) 50%, #1f1f22 100%);
  }
  .front-brand {
    position: absolute; inset: 0;
    display: flex; align-items: center; justify-content: center; gap: 14px;
  }
  .brand-square { width: 22px; height: 22px; background: var(--green); }
  .brand-name {
    color: var(--white); font-weight: 700; font-size: 38px; letter-spacing: 1px;
  }

  /* Back */
  .card-back { left: 520px; top: 410px; background: var(--card-dark); }
  .back-shape { position: absolute; inset: 0; }
  .back-brand {
    position: absolute; left: 42px; top: 40px;
    display: flex; align-items: center; gap: 10px;
  }
  .back-brand .brand-square { width: 16px; height: 16px; }
  .back-brand .brand-name { font-size: 26px; }

  .name-bar {
    position: absolute; left: 0; top: 142px; width: 7px; height: 52px;
    background: var(--green);
  }
  .person { position: absolute; left: 40px; top: 136px; }
  .person-name { font-size: 30px; line-height: 1.05; color: var(--white); font-weight: 300; }
  .person-name .first { color: var(--green); font-weight: 900; }
  .person-role { font-size: 14px; color: var(--muted); margin-top: 3px; }

  .contacts { position: absolute; left: 40px; top: 205px; list-style: none; }
  .contacts li {
    display: flex; align-items: center; gap: 10px;
    font-size: 13px; color: var(--white); height: 22px;
  }
  .contacts svg { width: 14px; height: 14px; flex: none; }
  .accent { color: var(--green); }
</style>
</head>
<body>
<main class="stage">

  <section class="card card-front" aria-label="Business card front">
    <div class="front-texture" role="img" aria-label="Embossed chevron texture pattern"></div>
    <div class="front-brand">
      <span class="brand-square"></span>
      <span class="brand-name">TMW Home Crafting</span>
    </div>
  </section>

  <section class="card card-back" aria-label="Business card back">
    <svg class="back-shape" viewBox="0 0 560 320" preserveAspectRatio="none" aria-hidden="true">
      <polygon points="380,0 560,0 560,320 478,320 496,150" fill="#1a9a4a"/>
      <polyline points="360,0 486,150 468,320" fill="none" stroke="#3a3a3f" stroke-width="8"/>
    </svg>

    <div class="back-brand">
      <span class="brand-square"></span>
      <span class="brand-name">TMW Home Crafting</span>
    </div>

    <div class="name-bar"></div>
    <div class="person">
      <p class="person-name"><span class="first">Liam</span> Hartley</p>
      <p class="person-role">General Manager</p>
    </div>

    <ul class="contacts">
      <li>
        <svg viewBox="0 0 24 24"><path fill="#1a9a4a" d="M6.6 10.8a15 15 0 0 0 6.6 6.6l2.2-2.2a1 1 0 0 1 1-.25 11 11 0 0 0 3.6.6 1 1 0 0 1 1 1V20a1 1 0 0 1-1 1A17 17 0 0 1 3 4a1 1 0 0 1 1-1h3.5a1 1 0 0 1 1 1 11 11 0 0 0 .6 3.6 1 1 0 0 1-.25 1z"/></svg>
        0400 123 456
      </li>
      <li>
        <svg viewBox="0 0 24 24"><circle cx="12" cy="12" r="9" fill="none" stroke="#1a9a4a" stroke-width="2.5"/><path d="M3 12h18M12 3c3 3 3 15 0 18M12 3c-3 3-3 15 0 18" fill="none" stroke="#1a9a4a" stroke-width="2"/></svg>
        <span>www.<span class="accent">tmwhomecrafting</span>.com.au</span>
      </li>
      <li>
        <svg viewBox="0 0 24 24"><rect x="2" y="5" width="20" height="14" rx="2" fill="none" stroke="#1a9a4a" stroke-width="2.5"/><path d="M3 6l9 7 9-7" fill="none" stroke="#1a9a4a" stroke-width="2.5"/></svg>
        <span>info@<span class="accent">tmwhomecrafting</span>.com.au</span>
      </li>
      <li>
        <svg viewBox="0 0 24 24"><path fill="#1a9a4a" d="M12 2a7 7 0 0 0-7 7c0 5 7 13 7 13s7-8 7-13a7 7 0 0 0-7-7zm0 9.5A2.5 2.5 0 1 1 12 6.5a2.5 2.5 0 0 1 0 5z"/></svg>
        Riverton, Tasmania, Australia
      </li>
    </ul>
  </section>

</main>
</body>
</html>
```